Verpackungen für Shampoos
Zielgruppe
Wir sind ein kleines Familienunternehmen mit 2-3 Friseurfilialen und Onlineshop im Naturfriseurbereich, arbeiten mit ökologischen, nachhaltigen und natürlichen Produkten und vertreiben unsere eigene Haarbürste. Wir betreiben mit Sol Verde unsere eigene Marke in diesem Bereich. Erste Produkte, wie eine eigene Haarbürste sind bereits vorhanden und entstanden.
Für unsere erste Shampoo Serie suchen wir ein klares, cleanes und hochwertiges Design. Die 200ml Shampooflasche kommt komplett in weiß und besteh aus recyceltem Material. Es soll klar die ökologisch nachhaltige und etwas höherpreisige Marke kommuniziert werden. Dabei sehen wir vom Stil „weniger ist mehr“ als ganz klare Designvorgabe. Anbei auch ein Beispiel von Pavura, die das ganze sehr schön umgesetzt haben.
Die INCI sind noch nicht final. Es wäre schön, wenn hier ein Platzhalter eingefügt würde. Da eine der Hauptzielgruppen auch Österreicher sind, würden wir uns über ein kleines „Made in Austria“ auf der Vorderseite (evtl. ganz unten auf der Flasche) freuen.
Insgesamt sind es vier verschiedene Shampoos, die aus der gleichen Serie stammen. Es wäre schön, wenn man diese auch direkt unterscheiden könnte. Vielleicht durch ein grafisches Element, oder einfach nur durch die verschiedenen Namenserweiterungen. Hier die Aufstellung mit den Erweiterungen:
Es werden 4 verschiedene Shampoos, die Namen sind:
Change - Strapaziertes Haar
Care - Normales Haar
Sensitiv - Empfindliche Kopfhaut
Balancing - Fettiges Haar
Zielgruppe:
Weiblich, 30-60 Jahre, mittleres bis gehobenes Einkommen, nachhaltig, ökologisch, natürlich, legt Wert auf hochwertige Produkte und Dienstleistungen, achtet auf Konsum.
Aufgabenstellung
Die Landingpage zur Bürste ist hier erreichbar (Beispiel):
Vielleicht hilft das etwas um das Design und die Tonality aufzuschnappen: https://sol-verde.de/gold-birch-wildschweinborstenbuerste/
Es wäre super, wenn das Design der Flasche ähnlich klar und strukturiert ist.
Die Shampoos sind komplett vegan und made in Austria. Die beiden Aspekte sollten in Design auch aufgegriffen werden. Da wir einen 4 farbigen Tamponade/Siebdruck auf der Flasche anwenden, stehen leider nicht so viele Farben zur Verfügung (3-4).
Link zur Flasche:
https://www.brumoxa.com/de/kosmetik/varleno/varleno-tubica/flasche-heavy-200ml-24-410-plastik
Des Weiteren kann sich noch am Sol Verde Haarkonzept und unserem Dienstleistungsflyer orientiert werden.
Benefits:
-       Pflegt das Haar, hält es geschmeidig
- Bio Shampoo Konzentrat
-       Die Grundlage für gesunde Kopfhaut und schönes Haar*
-       Vermindert Spliss*
-       Hält die Haare natürlich geschmeidig
-       Regt die Durchblutung der Kopfhaut an
-       Verteilt Nährstoffe von der Wurzel bis in die Spitzen*
-       Verbessert das Kopfhautklima*
-       Für eine gut durchblutete und gesunde Kopfhaut mit glänzenden und
geschmeidigen Haaren*
-       Entfernt Schuppen und abgestorbene Hautpartikel
-       Verbessert natürlich die allgemeine Haarstruktur
-       Entwirrt langes und gelocktes Haar
-       Reinigt die Kopfhaut ohne Chemie*
-       Mehr Volumen im Haar
-       Mehr Stand im Haar durch Kräftigung der Haarbalkmuskulatur
-       Spart Shampoo und hilft Shampoo seltener und weniger zu nutzen
-       Nährstoffversorgung bis in die Haarspitzen
Inhaltsstoffe:
Care
Aloe Vera Direktsaft*, Decyl Glucoside, Coco Glucoside, Lauryl Glucoside, Hopfenextrakt*, Pentylene Glycol green, Meli..

```html
<!DOCTYPE html>
<html lang="de">
<head>
<meta charset="utf-8">
<title>Sol Verde – Shampoo Serie</title>
<link href="https://fonts.googleapis.com/css2?family=Cormorant+Garamond:wght@300;400;500&family=Josefin+Sans:ital,wght@0,300;1,300&display=swap" rel="stylesheet">
<style>
  :root{
    --accent:#e0452c;
    --muted:#a39692;
    --blush:#d9bdb5;
    --paper:#ffffff;
    --stage:#ffffff;
    --edge:#ebe7e5;
    --gold-a:#b8923f;
    --gold-b:#f3dc9a;
    --cap-black:#0b0b0b;
  }
  *{box-sizing:border-box;margin:0;padding:0}
  html,body{width:1200px;height:1196px;overflow:hidden;background:var(--stage)}
  .sheet{position:relative;width:1200px;height:1196px}
  .card{position:absolute;width:563px;height:563px;background:var(--paper);
    box-shadow:2px 3px 8px rgba(0,0,0,.18)}
  .card--tl{left:22px;top:22px}
  .card--tr{left:614px;top:22px}
  .card--bl{left:22px;top:607px}
  .card--br{left:614px;top:607px}

  .bottle{position:absolute;top:47px;width:157px;height:479px}
  .bottle--front{left:63px}
  .bottle--back{left:348px}
  .cap{position:absolute;left:30px;top:0;width:98px;height:61px;
    background:linear-gradient(90deg,var(--gold-a),var(--gold-b) 22%,var(--gold-a) 30%,var(--cap-black) 30%,var(--cap-black) 68%,var(--gold-a) 68%,var(--gold-b) 82%,var(--gold-a))}
  .body{position:absolute;left:0;top:61px;width:157px;height:418px;background:var(--paper);
    border:1px solid var(--edge);border-radius:6px 6px 16px 16px/6px 6px 8px 8px;
    box-shadow:inset 6px 0 10px rgba(0,0,0,.03),inset -6px 0 10px rgba(0,0,0,.05)}

  .brand{position:absolute;top:50px;left:32px;display:flex;align-items:center;gap:3px;
    font-family:"Cormorant Garamond",serif;font-size:12px;color:var(--muted)}
  .brand-dot{width:14px;height:14px;border-radius:50%;background:var(--blush)}
  .brand-rule{position:absolute;top:68px;left:68px;width:52px;height:1px;background:var(--blush)}

  .front-text{position:absolute;left:0;width:100%;text-align:center;font-family:"Cormorant Garamond",serif}
  .variant{top:183px;font-size:19px;font-weight:400;letter-spacing:4px;color:var(--accent);white-space:nowrap}
  .variant-sub{top:205px;font-size:12px;font-weight:300;color:var(--accent);white-space:nowrap}
  .claim{top:225px;font-size:9px;font-weight:300;color:var(--muted);white-space:nowrap}
  .product{top:330px;font-size:12px;letter-spacing:3px;color:var(--accent)}
  .origin{top:384px;font-size:9px;font-weight:300;color:var(--muted)}

  .benefits{position:absolute;left:12px;top:69px;width:140px;list-style:none;
    font-family:"Josefin Sans",sans-serif;font-weight:300;font-size:7.4px;line-height:9.6px;color:var(--accent)}
  .benefits li{position:relative;padding-left:7px;margin-bottom:5.3px}
  .benefits li::before{content:"";position:absolute;left:0;top:2.5px;width:3px;height:3px;background:var(--accent);transform:rotate(45deg)}
  .ingredients{position:absolute;left:16px;top:249px;width:128px;
    font-family:"Josefin Sans",sans-serif;font-weight:300;font-size:5.9px;line-height:8.1px;color:var(--muted)}
  .ingredients em{display:block}
  .vegan-badge{position:absolute;left:62px;top:354px;width:30px;height:30px;border-radius:50%;
    border:1px solid var(--edge);background:radial-gradient(circle,#efebe9 0 45%,var(--paper) 46%)}
  .volume{position:absolute;left:100px;top:362px;font-family:"Josefin Sans",sans-serif;font-weight:300;font-size:13px;color:var(--accent)}
</style>
</head>
<body>
<main class="sheet">

  <!-- CHANGE -->
  <section class="card card--tl">
    <div class="bottle bottle--front"><div class="cap"></div><div class="body">
      <div class="brand">Sol Verde <span class="brand-dot"></span></div><div class="brand-rule"></div>
      <p class="front-text variant">CHANGE</p>
      <p class="front-text variant-sub">strapaziertes Haar</p>
      <p class="front-text claim">100 % vegan | 100 % natural</p>
      <p class="front-text product">SHAMPOO</p>
      <p class="front-text origin">Made in Austria</p>
    </div></div>
    <div class="bottle bottle--back"><div class="cap"></div><div class="body">
      <ul class="benefits">
        <li>Bio Shampoo Konzentrat</li><li>Vermindert Spliss*</li><li>Verbessert das Kopfhautklima*</li><li>Mehr Volumen im Haar</li><li>Entfernt Schuppen und abgestor-bene Hautpartikel</li><li>Entwirrt langes und gelocktes Haar</li><li>Reinigt die Kopfhaut ohne Chemie*</li><li>Nährstoffversorgung bis in die Haarspitzen</li><li>Regt die Durchblutung der Kopfhaut an</li>
      </ul>
      <p class="ingredients"><em>Inhaltsstoffe:</em>Aloe Vera Direktsaft*, Decyl Glucoside, Coco Glucoside, Lauryl Glucoside, Hopfenextrakt*, Pentylene Glycol green, Melissenblätter-Extrakt*, Arganöl*, Brokkolisamenöl*, Xanthan Gum, Parfümöl natürlich 'Maiglöckchen', Lorem ipsum dolor sit amet, consectetuer adipiscing elit, sed diam nonummy nibh euismod tincidunt ut laoreet dolore magna aliquam erat</p>
      <span class="vegan-badge"></span><span class="volume">200 ml</span>
    </div></div>
  </section>

  <!-- CARE -->
  <section class="card card--tr">
    <div class="bottle bottle--front"><div class="cap"></div><div class="body">
      <div class="brand">Sol Verde <span class="brand-dot"></span></div><div class="brand-rule"></div>
      <p class="front-text variant">CARE</p>
      <p class="front-text variant-sub">normales Haar</p>
      <p class="front-text claim">100 % vegan | 100 % natural</p>
      <p class="front-text product">SHAMPOO</p>
      <p class="front-text origin">Made in Austria</p>
    </div></div>
    <div class="bottle bottle--back"><div class="cap"></div><div class="body">
      <ul class="benefits">
        <li>Bio Shampoo Konzentrat</li><li>Vermindert Spliss*</li><li>Verbessert das Kopfhautklima*</li><li>Mehr Volumen im Haar</li><li>Entfernt Schuppen und abgestor-bene Hautpartikel</li><li>Entwirrt langes und gelocktes Haar</li><li>Reinigt die Kopfhaut ohne Chemie*</li><li>Nährstoffversorgung bis in die Haarspitzen</li><li>Regt die Durchblutung der Kopfhaut an</li>
      </ul>
      <p class="ingredients"><em>Inhaltsstoffe:</em>Aloe Vera Direktsaft*, Decyl Glucoside, Coco Glucoside, Lauryl Glucoside, Hopfenextrakt*, Pentylene Glycol green, Melissenblätter-Extrakt*, Arganöl*, Brokkolisamenöl*, Xanthan Gum, Parfümöl natürlich 'Maiglöckchen', Lorem ipsum dolor sit amet, consectetuer adipiscing elit, sed diam nonummy nibh euismod tincidunt ut laoreet dolore magna aliquam erat</p>
      <span class="vegan-badge"></span><span class="volume">200 ml</span>
    </div></div>
  </section>

  <!-- SENSITIV -->
  <section class="card card--bl">
    <div class="bottle bottle--front"><div class="cap"></div><div class="body">
      <div class="brand">Sol Verde <span class="brand-dot"></span></div><div class="brand-rule"></div>
      <p class="front-text variant">SENSITIV</p>
      <p class="front-text variant-sub">empfindliche Kopfhaut</p>
      <p class="front-text claim">100 % vegan | 100 % natural</p>
      <p class="front-text product">SHAMPOO</p>
      <p class="front-text origin">Made in Austria</p>
    </div></div>
    <div class="bottle bottle--back"><div class="cap"></div><div class="body">
      <ul class="benefits">
        <li>Bio Shampoo Konzentrat</li><li>Vermindert Spliss*</li><li>Verbessert das Kopfhautklima*</li><li>Mehr Volumen im Haar</li><li>Entfernt Schuppen und abgestor-bene Hautpartikel</li><li>Entwirrt langes und gelocktes Haar</li><li>Reinigt die Kopfhaut ohne Chemie*</li><li>Nährstoffversorgung bis in die Haarspitzen</li><li>Regt die Durchblutung der Kopfhaut an</li>
      </ul>
      <p class="ingredients"><em>Inhaltsstoffe:</em>Aloe Vera Direktsaft*, Decyl Glucoside, Coco Glucoside, Lauryl Glucoside, Hopfenextrakt*, Pentylene Glycol green, Melissenblätter-Extrakt*, Arganöl*, Brokkolisamenöl*, Xanthan Gum, Parfümöl natürlich 'Maiglöckchen', Lorem ipsum dolor sit amet, consectetuer adipiscing elit, sed diam nonummy nibh euismod tincidunt ut laoreet dolore magna aliquam erat</p>
      <span class="vegan-badge"></span><span class="volume">200 ml</span>
    </div></div>
  </section>

  <!-- BALANCING -->
  <section class="card card--br">
    <div class="bottle bottle--front"><div class="cap"></div><div class="body">
      <div class="brand">Sol Verde <span class="brand-dot"></span></div><div class="brand-rule"></div>
      <p class="front-text variant">BALANCING</p>
      <p class="front-text variant-sub">fettiges Haar</p>
      <p class="front-text claim">100 % vegan | 100 % natural</p>
      <p class="front-text product">SHAMPOO</p>
      <p class="front-text origin">Made in Austria</p>
    </div></div>
    <div class="bottle bottle--back"><div class="cap"></div><div class="body">
      <ul class="benefits">
        <li>Bio Shampoo Konzentrat</li><li>Vermindert Spliss*</li><li>Verbessert das Kopfhautklima*</li><li>Mehr Volumen im Haar</li><li>Entfernt Schuppen und abgestor-bene Hautpartikel</li><li>Entwirrt langes und gelocktes Haar</li><li>Reinigt die Kopfhaut ohne Chemie*</li><li>Nährstoffversorgung bis in die Haarspitzen</li><li>Regt die Durchblutung der Kopfhaut an</li>
      </ul>
      <p class="ingredients"><em>Inhaltsstoffe:</em>Aloe Vera Direktsaft*, Decyl Glucoside, Coco Glucoside, Lauryl Glucoside, Hopfenextrakt*, Pentylene Glycol green, Melissenblätter-Extrakt*, Arganöl*, Brokkolisamenöl*, Xanthan Gum, Parfümöl natürlich 'Maiglöckchen', Lorem ipsum dolor sit amet, consectetuer adipiscing elit, sed diam nonummy nibh euismod tincidunt ut laoreet dolore magna aliquam erat</p>
      <span class="vegan-badge"></span><span class="volume">200 ml</span>
    </div></div>
  </section>

</main>
</body>
</html>
```